Executive Business Card for Healthcare Company [Need Today]

I need a business card design for a healthcare company. The only branding the company has thus far is a logo. The cards will be utilized by company executives. The design I envision will be vibrant and appealing but with a corporate feel. They shouldn't be too casual or playful. I would like to complete this project TODAY if possible.

Target Market(s)

Healthcare vendors, other executives in healthcare and pharmaceuticals

Industry/Entity Type

Pharmaceutical

Contact Information for Business Card

See attachment

Font styles to use
Serif
Sans Serif

Colors

Designer to choose colors to be used in the design.

```html
<!DOCTYPE html>
<html lang="en">
<head>
<meta charset="utf-8">
<title>Corvela Therapeutics – Business Card</title>
<link rel="stylesheet" href="https://fonts.googleapis.com/css2?family=Crimson+Text:wght@400;600&family=Open+Sans:wght@300;400&display=swap">
<style>
  :root {
    --backdrop: #8fa7ad;
    --paper: #ffffff;
    --teal: #3bbfc8;
    --green: #6cc49a;
    --ink: #1f1f1f;
    --rule: #9a9a9a;
    --icon-ink: #222222;
  }
  * { box-sizing: border-box; margin: 0; padding: 0; }
  html, body {
    width: 1200px; height: 800px; overflow: hidden;
    background: var(--backdrop);
  }
  .canvas { position: relative; width: 1200px; height: 800px; }

  .card {
    position: absolute; left: 326px; width: 538px; height: 307px;
    background: var(--paper); overflow: hidden;
  }
  .card--front { top: 24px; }
  .card--back { top: 426px; }

  .card__art { position: absolute; inset: 0; width: 100%; height: 100%; }

  .brand { position: absolute; font-family: "Open Sans", sans-serif; font-weight: 300; color: var(--teal); line-height: 1; }
  .brand__name { display: block; letter-spacing: 1px; }
  .brand__sub { display: block; text-align: right; }

  .card--front .brand { left: 136px; top: 124px; }
  .card--front .brand__name { font-size: 44px; }
  .card--front .brand__sub { font-size: 22px; margin-top: 2px; }

  .card--back .brand { left: 110px; top: 30px; }
  .card--back .brand__name { font-size: 36px; }
  .card--back .brand__sub { font-size: 18px; margin-top: 2px; }

  .website {
    position: absolute; left: 0; right: 0; top: 276px; text-align: center;
    font-family: "Crimson Text", serif; font-size: 14px; color: var(--teal);
  }

  .person { position: absolute; left: 34px; top: 100px; font-family: "Crimson Text", serif; color: var(--ink); }
  .person__name { font-size: 28px; font-weight: 400; line-height: 1.1; }
  .person__title { font-size: 13.5px; line-height: 1.2; }

  .contact { position: absolute; left: 341px; top: 90px; list-style: none; color: var(--paper); }
  .contact__item { position: absolute; left: 0; display: flex; align-items: center; white-space: nowrap; }
  .contact__icon {
    width: 28px; height: 28px; border-radius: 50%; background: var(--paper);
    display: flex; align-items: center; justify-content: center; flex: none;
  }
  .contact__icon svg { width: 15px; height: 15px; fill: var(--icon-ink); }
  .contact__text { margin-left: 9px; font-family: "Open Sans", sans-serif; }
  .contact__item--email { top: 1px; } .contact__item--email .contact__text { font-size: 14.5px; }
  .contact__item--office { top: 40px; } .contact__item--office .contact__text { font-size: 13px; }
  .contact__item--mobile { top: 82px; } .contact__item--mobile .contact__text { font-size: 19.5px; margin-left: 11px; }
  .contact__item--address { top: 120px; align-items: flex-start; }
  .contact__item--address .contact__icon { width: 26px; height: 26px; }
  .contact__item--address .contact__text {
    font-family: "Crimson Text", serif; font-size: 15.5px; line-height: 1.3; margin-left: 4px; margin-top: 1px;
  }

  .social { position: absolute; left: 51px; top: 246px; text-align: center; }
  .social__label { font-family: "Crimson Text", serif; font-size: 16.5px; color: var(--ink); margin-left: 10px; }
  .social__list { display: flex; gap: 7px; margin-top: 6px; list-style: none; }
  .social__list li { width: 18px; height: 18px; background: var(--paper); opacity: 0.9; }
</style>
</head>
<body>
<main class="canvas">

  <section class="card card--front" aria-label="Card front">
    <svg class="card__art" viewBox="0 0 538 307" aria-hidden="true">
      <defs>
        <linearGradient id="frameGrad" x1="0" y1="0" x2="0" y2="1">
          <stop offset="0" stop-color="#6cc49a"/>
          <stop offset="1" stop-color="#3bbfc8"/>
        </linearGradient>
        <clipPath id="frontInner"><rect x="9" y="8" width="520" height="290"/></clipPath>
      </defs>
      <rect x="4" y="4" width="530" height="299" fill="none" stroke="url(#frameGrad)" stroke-width="9"/>
      <circle clip-path="url(#frontInner)" cx="498" cy="162" r="138" fill="none" stroke="#6cc49a" stroke-width="13"/>
      <circle cx="64" cy="150" r="50" fill="none" stroke="#6cc49a" stroke-width="4.5"/>
      <line x1="127" y1="130" x2="127" y2="182" stroke="#9a9a9a" stroke-width="1.2"/>
    </svg>
    <div class="brand">
      <span class="brand__name">corvela</span>
      <span class="brand__sub">therapeutics</span>
    </div>
    <p class="website">www.website.com</p>
  </section>

  <section class="card card--back" aria-label="Card back">
    <svg class="card__art" viewBox="0 0 538 307" aria-hidden="true">
      <defs>
        <linearGradient id="waveGrad" x1="0" y1="1" x2="1" y2="0">
          <stop offset="0" stop-color="#3bbfc8"/>
          <stop offset="1" stop-color="#6cc49a"/>
        </linearGradient>
      </defs>
      <path d="M0,200 C60,238 120,246 172,224 C228,200 252,142 300,110 C352,74 430,56 538,88 L538,307 L0,307 Z" fill="url(#waveGrad)"/>
      <circle cx="53" cy="52" r="38" fill="none" stroke="#6cc49a" stroke-width="3.5"/>
      <line x1="101" y1="36" x2="101" y2="76" stroke="#9a9a9a" stroke-width="1.2"/>
    </svg>
    <div class="brand">
      <span class="brand__name">corvela</span>
      <span class="brand__sub">therapeutics</span>
    </div>

    <div class="person">
      <h1 class="person__name">Daniel Marsh</h1>
      <p class="person__title">Senior Director of Marketing</p>
    </div>

    <ul class="contact">
      <li class="contact__item contact__item--email">
        <span class="contact__icon"><svg viewBox="0 0 16 16"><path d="M1 3h14v10H1z M1.5 3.5 8 9l6.5-5.5" fill="#222" stroke="#fff" stroke-width="1"/></svg></span>
        <span class="contact__text">dmarsh@corvelarx.com</span>
      </li>
      <li class="contact__item contact__item--office">
        <span class="contact__icon"><svg viewBox="0 0 16 16"><path d="M1 6c0-2 3-3 7-3s7 1 7 3v1h-3V5.5H4V7H1z M4 8h8l2 6H2z"/></svg></span>
        <span class="contact__text">555-204-7731</span>
      </li>
      <li class="contact__item contact__item--mobile">
        <span class="contact__icon"><svg viewBox="0 0 16 16"><path d="M3.5 1 6 4 4.6 5.7c.8 2.3 3.4 4.9 5.7 5.7L12 10l3 2.5-1.5 2.5C8 15 1 8 1 2.5z"/></svg></span>
        <span class="contact__text">555-318-6642</span>
      </li>
      <li class="contact__item contact__item--address">
        <span class="contact__icon"><svg viewBox="0 0 16 16"><path d="M8 1a5 5 0 0 1 5 5c0 4-5 9-5 9S3 10 3 6a5 5 0 0 1 5-5zm0 3a2 2 0 1 0 0 4 2 2 0 0 0 0-4z"/></svg></span>
        <span class="contact__text">118 Linden Avenue<br>Fairview OH 44120</span>
      </li>
    </ul>

    <div class="social">
      <p class="social__label">Find Us on:</p>
      <ul class="social__list" aria-label="Social profiles">
        <li></li><li></li><li></li><li></li>
      </ul>
    </div>
  </section>

</main>
</body>
</html>
```